Tidy4all

Full service cleaning company. Specializing in commercial and apartment cleans.
Fully licensed and insured
Digital photos and invoices provided
for every job
For web designer...basic info as expected by a highend cleaning company that provides excellent service at reasonable pricing. We are going after large property management companies as well as not pricing ourselves out to help the local mom and pop companies as well.
Updates

Project Deadline Extended Reason: Everyone seems to be having trouble understanding that we are a dumpster company that is adding a cleaning side to the company. We want our clients to see Tidy4All as a separate branch of our our already established waste management company.We are not a regular cleaning company. We specialize in going after large commercial cleans and apartment cleans. I have now included info regarding a proposal for work and our invoice/job completion to make it clearer what we do Added Monday, July 20, 2015

Target Market(s)

Property Management companies in Savannah, Richmond Hill, Rincon, Hinesville and Midway Georgia

Industry/Entity Type

Cleaning Service

Coding

Coded - Design and coding required

Number of Pages Required

3 page

Requirements
Must have
• Nice home page with lots of photos (stock are fine) to convey exactly what we do (getting logo bid on right now on this sight).
• Information page with employee photos (can leave blank) need room for 4 photos and bios.
• Page or link to a static page for the dumpster company BinRun (logo for this is red and black file attached along with photo of dumpster. This page just needs to be one page with contact info and information about commercial dumpster.
• Basically this site is just a fluff page used for marketing purposes. Its content can be general and once created wont change much. Services and photos can be provided upon request but general layout and info is what we are looking for.

```html
<!DOCTYPE html>
<html lang="en">
<head>
<meta charset="utf-8">
<title>Tidy4All</title>
<link href="https://fonts.googleapis.com/css2?family=Open+Sans:wght@400;600;700&family=PT+Serif:wght@400;700&display=swap" rel="stylesheet">
<style>
:root{
  --red:#e0231b;
  --ink:#2a2a2a;
  --text:#777;
  --muted:#9a9a9a;
  --band:#ececec;
  --lime:#8dbb1c;
  --footer:#1f1f1f;
  --footer-bottom:#141414;
  --white:#fff;
}
*{box-sizing:border-box;margin:0;padding:0}
html,body{width:681px;height:1200px;overflow:hidden}
body{background:var(--white);font-family:"Open Sans",Arial,sans-serif;color:var(--text);font-size:7px;line-height:1.45}

.site-header{height:60px;position:relative}
.brand{position:absolute;left:48px;top:17px;display:flex;align-items:center;gap:7px}
.brand-mark{width:18px;height:18px;background:var(--red)}
.brand-name{font-family:"Open Sans",Arial,sans-serif;font-weight:600;font-size:18px;color:var(--ink);letter-spacing:.2px}
.contact-strip{position:absolute;right:24px;top:10px;display:flex;align-items:center;gap:12px;font-size:8px;color:var(--ink)}
.contact-strip .mail{display:flex;align-items:center;gap:4px}
.phone-pill{background:var(--red);color:var(--white);font-weight:700;font-size:11px;padding:3px 9px 3px 6px;border-radius:3px;display:flex;align-items:center;gap:5px}

.main-nav{height:22px;margin-left:215px;background:var(--red);display:flex;align-items:stretch;padding-left:8px}
.main-nav a{color:var(--white);text-decoration:none;font-size:8px;font-weight:600;padding:0 13px;display:flex;align-items:center}
.main-nav a.active{background:var(--ink)}

.hero{position:relative;height:252px;background:linear-gradient(90deg,#d9dde2 0%,#eef0f2 30%,#9fb4c9 55%,#6f8dad 80%,#4e6e91 100%)}
.hero-caption{position:absolute;left:250px;top:70px;width:182px;background:rgba(20,20,20,.78);padding:12px 10px;text-align:center}
.hero-caption h1{font-size:13px;color:var(--white);font-weight:700;line-height:1.25}
.hero-caption p{font-size:12px;color:var(--red);font-weight:700;line-height:1.25;margin-top:6px}
.hero-arrow{position:absolute;top:116px;width:18px;height:18px;border-radius:50%;background:var(--white);display:flex;align-items:center;justify-content:center}
.hero-arrow.prev{left:12px}.hero-arrow.next{right:12px}

.service-cards{display:flex;gap:18px;padding:24px 48px 22px}
.card{flex:1;border-top:3px solid var(--red);box-shadow:0 1px 4px rgba(0,0,0,.18);padding:8px 9px 9px;height:182px}
.card h2{font-family:"PT Serif",Georgia,serif;font-size:13px;color:var(--ink);margin-bottom:6px}
.card .photo{height:66px;margin-bottom:6px}
.read-more{display:block;text-align:right;color:var(--red);font-size:6.5px;font-weight:700;margin-top:5px}

.welcome-band{background:var(--band);height:205px;display:flex;gap:26px;padding:22px 48px}
.welcome{flex:1.7}
.welcome h2,.schedule h2{font-family:"PT Serif",Georgia,serif;font-size:13px;color:var(--ink);margin-bottom:8px}
.welcome p{margin-bottom:7px}
.schedule{flex:1}
.schedule form{display:flex;flex-wrap:wrap;gap:4px}
.field{background:var(--white);border:1px solid #d6d6d6;height:14px;width:100%;font-size:6px;color:var(--muted);padding:2px 4px}
.field.half{width:calc(50% - 2px)}
.field.message{height:34px}
.send-btn{margin-left:auto;background:var(--red);color:var(--white);font-size:6.5px;font-weight:700;padding:3px 10px}

.features{display:flex;gap:20px;padding:20px 48px 0;height:198px}
.feature{flex:1}
.feature h3{font-family:"PT Serif",Georgia,serif;font-size:12px;color:var(--ink);margin-bottom:7px}
.feature .photo{height:58px;margin-bottom:6px}
.why-list{list-style:none}
.why-list li{display:flex;gap:4px;align-items:center;margin-bottom:5px;font-size:6.5px}

.cta{margin:0 48px;background:var(--lime);height:64px;display:flex;align-items:center;justify-content:center;gap:10px;color:var(--white)}
.cta p{font-family:"PT Serif",Georgia,serif;font-size:11px;font-weight:700}
.cta .zip{background:var(--white);width:70px;height:14px;font-size:6px;color:var(--muted);padding:2px 4px}
.cta .btn{background:var(--ink);font-size:6.5px;font-weight:700;padding:3px 8px}

.site-footer{margin-top:22px;background:var(--footer);height:128px;display:flex;gap:22px;padding:14px 48px;color:#bbb}
.site-footer h4{color:var(--white);font-size:8px;font-weight:700;margin-bottom:6px}
.site-footer ul{list-style:none}
.site-footer li{margin-bottom:2px;font-size:6.5px}
.foot-links{width:95px}.foot-contact{width:130px}.foot-faq{width:150px}
.foot-brand{flex:1;display:flex;align-items:center;justify-content:flex-end;gap:6px}
.foot-brand .brand-mark{background:#555}
.foot-brand span.name{font-family:"Open Sans",Arial,sans-serif;font-weight:600;font-size:16px;color:#666}
.foot-row{display:flex;gap:4px;margin-bottom:4px}
.faq-more{color:var(--white);font-size:6.5px;font-weight:700}
.legal{background:var(--footer-bottom);height:21px;padding:0 48px;display:flex;align-items:center;color:#999;font-size:6px}
</style>
</head>
<body>

<header class="site-header">
  <div class="brand"><span class="brand-mark"></span><span class="brand-name">Tidy4All</span></div>
  <div class="contact-strip">
    <span class="mail"><svg width="10" height="7" viewBox="0 0 10 7"><rect x=".5" y=".5" width="9" height="6" fill="none" stroke="#e0231b"/><path d="M.5.5 5 4 9.5.5" fill="none" stroke="#e0231b"/></svg>info@tidy4all.com</span>
    <span class="phone-pill"><svg width="9" height="9" viewBox="0 0 24 24"><path fill="#fff" d="M6.6 10.8a15 15 0 0 0 6.6 6.6l2.2-2.2c.3-.3.7-.4 1-.2 1.1.4 2.3.6 3.6.6.6 0 1 .4 1 1V20c0 .6-.4 1-1 1A17 17 0 0 1 3 4c0-.6.4-1 1-1h3.5c.6 0 1 .4 1 1 0 1.2.2 2.4.6 3.6.1.3 0 .7-.2 1z"/></svg>123.456.7890</span>
  </div>
</header>

<nav class="main-nav">
  <a class="active">Home</a><a>About Us</a><a>Services</a><a>Think Green</a><a>Customer Reviews</a><a>Contact Us</a>
</nav>

<section class="hero" role="img" aria-label="Garbage truck on a street beside tall glass office towers">
  <div class="hero-caption">
    <h1>We Are A full Service Cleaning Company</h1>
    <p>Specializing in commercial and apartment cleans</p>
  </div>
  <span class="hero-arrow prev"><svg width="6" height="8" viewBox="0 0 6 8"><path d="M5 0 1 4l4 4" fill="none" stroke="#333" stroke-width="1.5"/></svg></span>
  <span class="hero-arrow next"><svg width="6" height="8" viewBox="0 0 6 8"><path d="m1 0 4 4-4 4" fill="none" stroke="#333" stroke-width="1.5"/></svg></span>
</section>

<section class="service-cards">
  <article class="card">
    <h2>Home Owner</h2>
    <div class="photo" role="img" aria-label="Roll-off dumpster filled with household debris" style="background:linear-gradient(135deg,#8a6a4f,#5d4b3e 60%,#a89a88)"></div>
    <p>We haul away renovation waste and clutter so your home stays clean. Simple booking, fair rates and fast pickup for every job, big or small, in your area.</p>
    <span class="read-more">READ MORE &gt;</span>
  </article>
  <article class="card">
    <h2>Business Owner</h2>
    <div class="photo" role="img" aria-label="Orange commercial dumpster behind a business" style="background:linear-gradient(135deg,#c8692e,#9a4a22 60%,#d9c2a8)"></div>
    <p>Commercial cleans and waste removal for offices, stores and property managers. Licensed, insured crews with photos and invoices provided after each visit.</p>
    <span class="read-more">READ MORE &gt;</span>
  </article>
  <article class="card">
    <h2>Rent-a-Dumpster</h2>
    <div class="photo" role="img" aria-label="Dumpster rental container parked on a driveway" style="background:linear-gradient(135deg,#9aa2ab,#5f6770 60%,#c9ccd0)"></div>
    <p>Choose the right size container for your project. We drop it off, you fill it, and we take it away on schedule with no hidden fees or long waits at all.</p>
    <span class="read-more">READ MORE &gt;</span>
  </article>
</section>

<section class="welcome-band">
  <div class="welcome">
    <h2>Welcome To Tidy4All</h2>
    <p>Tidy4All is the cleaning branch of an established waste management company. We focus on large commercial cleans and apartment turnovers, giving property managers one trusted partner for cleaning and hauling across the region.</p>
    <p>Our crews are fully licensed and insured, and every job comes with digital photos and a clear invoice. We keep pricing reasonable so local family businesses get the same careful service as large firms.</p>
    <span class="read-more">READ MORE &gt;</span>
  </div>
  <div class="schedule">
    <h2>Schedule A Service</h2>
    <form>
      <div class="field">Name</div>
      <div class="field">Phone</div>
      <div class="field half">Preferred Date</div><div class="field half">Time</div>
      <div class="field">Email</div>
      <div class="field message">Message</div>
      <span class="send-btn">Send</span>
    </form>
  </div>
</section>

<section class="features">
  <div class="feature">
    <h3>24/7 Access</h3>
    <div class="photo" role="img" aria-label="Sign reading 24H service" style="background:linear-gradient(135deg,#7b97b8,#3f5f86)"></div>
    <p>Reach our team any time of day. We answer calls around the clock and schedule urgent cleans fast.</p>
  </div>
  <div class="feature">
    <h3>Reliable. Clean. Safe.</h3>
    <div class="photo" role="img" aria-label="Row of green waste containers" style="background:linear-gradient(135deg,#5aa23a,#2f7a24 60%,#9bc47c)"></div>
    <p>Trained crews, safe equipment and careful work on every site, with results you can see in photos.</p>
  </div>
  <div class="feature">
    <h3>Why Choose Us</h3>
    <ul class="why-list">
      <li><svg width="7" height="7" viewBox="0 0 8 8"><path d="m1 4 2 2 4-5" fill="none" stroke="#e0231b" stroke-width="1.6"/></svg>Wide selection of container sizes</li>
      <li><svg width="7" height="7" viewBox="0 0 8 8"><path d="m1 4 2 2 4-5" fill="none" stroke="#e0231b" stroke-width="1.6"/></svg>Flexible, timely pickup and delivery</li>
      <li><svg width="7" height="7" viewBox="0 0 8 8"><path d="m1 4 2 2 4-5" fill="none" stroke="#e0231b" stroke-width="1.6"/></svg>Fair prices with no surprises</li>
      <li><svg width="7" height="7" viewBox="0 0 8 8"><path d="m1 4 2 2 4-5" fill="none" stroke="#e0231b" stroke-width="1.6"/></svg>Easy online ordering and scheduling</li>
      <li><svg width="7" height="7" viewBox="0 0 8 8"><path d="m1 4 2 2 4-5" fill="none" stroke="#e0231b" stroke-width="1.6"/></svg>Online account management</li>
      <li><svg width="7" height="7" viewBox="0 0 8 8"><path d="m1 4 2 2 4-5" fill="none" stroke="#e0231b" stroke-width="1.6"/></svg>Instant online pricing</li>
    </ul>
  </div>
</section>

<section class="cta">
  <p>Ready to get started? See what dumpsters are available in your area.</p>
  <span class="zip">Enter Zip Code</span>
  <span class="btn">SHOW PRODUCTS</span>
</section>

<footer class="site-footer">
  <div class="foot-links">
    <h4>Quick Links</h4>
    <ul><li>Home</li><li>About Us</li><li>Services</li><li>Think Green</li><li>Customer Reviews</li><li>Contact Us</li></ul>
  </div>
  <div class="foot-contact">
    <h4>Contact Information</h4>
    <div class="foot-row"><svg width="7" height="9" viewBox="0 0 10 13"><path d="M5 0a5 5 0 0 0-5 5c0 4 5 8 5 8s5-4 5-8a5 5 0 0 0-5-5zm0 7a2 2 0 1 1 0-4 2 2 0 0 1 0 4z" fill="#e0231b"/></svg><span>120 Harbor Lane, Suite 4<br>Savannah, GA 31401</span></div>
    <div class="foot-row"><svg width="8" height="8" viewBox="0 0 24 24"><path fill="#e0231b" d="M6.6 10.8a15 15 0 0 0 6.6 6.6l2.2-2.2c.3-.3.7-.4 1-.2 1.1.4 2.3.6 3.6.6.6 0 1 .4 1 1V20c0 .6-.4 1-1 1A17 17 0 0 1 3 4c0-.6.4-1 1-1h3.5c.6 0 1 .4 1 1 0 1.2.2 2.4.6 3.6.1.3 0 .7-.2 1z"/></svg><span>123.456.7890</span></div>
    <div class="foot-row"><svg width="8" height="6" viewBox="0 0 10 7"><rect x=".5" y=".5" width="9" height="6" fill="none" stroke="#e0231b"/><path d="M.5.5 5 4 9.5.5" fill="none" stroke="#e0231b"/></svg><span>info@tidy4all.com</span></div>
  </div>
  <div class="foot-faq">
    <h4>FAQ's</h4>
    <ul><li>What sizes of dumpster do you offer?</li><li>How much does a clean cost?</li><li>How long can I keep a dumpster?</li><li>What items are not allowed?</li></ul>
    <span class="faq-more">More FAQs</span>
  </div>
  <div class="foot-brand"><span class="brand-mark"></span><span class="name">Tidy4All</span></div>
</footer>
<div class="legal">© 2015 Tidy4All &nbsp;|&nbsp; All rights reserved</div>

</body>
</html>
```